New Business Card Design Project

Need a design that will create an impact / strong impression towards our clients for our business. We are in the lighting business and we do lighting retrofits for large commercial to industrial clientele.

Target Market(s)

Lighting Industry

Industry/Entity Type

Business

Font styles to use
Other font styles liked:
• we would like to use the font on our logo, not sure what it is though..

Requirements
Must have
• Our logo.
Nice to have
• We are open to suggestions that have to do with lighting.

```html
<!DOCTYPE html>
<html lang="en">
<head>
<meta charset="utf-8">
<title>Brightline Retrofit Group – Business Card</title>
<link rel="stylesheet" href="https://fonts.googleapis.com/css2?family=Roboto:wght@400;500&family=Roboto+Condensed:wght@500;700&display=swap">
<style>
  :root {
    --backdrop: #5b4838;
    --forest: #10380f;
    --emerald: #0a7d35;
    --leaf: #66bf55;
    --name-green: #2b9a40;
    --title-green: #6cc24a;
    --paper: #f2f2f2;
    --white: #ffffff;
  }
  * { margin: 0; padding: 0; box-sizing: border-box; }
  html, body { width: 1200px; height: 960px; overflow: hidden; }
  body {
    position: relative;
    background: var(--backdrop);
    font-family: "Roboto", Arial, sans-serif;
  }
  .card {
    position: absolute;
    width: 600px;
    height: 343px;
    overflow: hidden;
  }
  .card--front { left: 314px; top: 113px; background: var(--paper); }
  .card--back { left: 311px; top: 472px; background: var(--leaf); }

  .front-shapes { position: absolute; left: 0; top: 0; }

  .identity { position: absolute; left: 36px; top: 36px; color: var(--white); }
  .identity__name {
    font-family: "Roboto Condensed", Arial, sans-serif;
    font-weight: 700;
    font-size: 22px;
    color: var(--name-green);
    letter-spacing: 0.2px;
  }
  .identity__title {
    font-family: "Roboto Condensed", Arial, sans-serif;
    font-weight: 500;
    font-size: 15px;
    color: var(--title-green);
    margin-top: 2px;
  }
  .identity__address { font-size: 14.5px; line-height: 19px; margin-top: 10px; }

  .contacts {
    position: absolute; left: 36px; top: 216px;
    list-style: none; color: var(--white); font-size: 14.5px;
  }
  .contacts li { display: flex; align-items: center; height: 19px; }
  .contacts svg { width: 13px; height: 13px; margin-right: 9px; fill: var(--white); }

  .company-mark {
    position: absolute; left: 328px; top: 244px;
    display: flex; align-items: center; gap: 10px;
    font-family: "Roboto", Arial, sans-serif; font-weight: 500;
    color: var(--forest);
  }
  .company-mark__square { width: 14px; height: 14px; background: var(--forest); }
  .company-mark__name { font-size: 19px; line-height: 23px; letter-spacing: 0.5px; }

  .back-mark {
    position: absolute; left: 0; right: 0; top: 130px;
    text-align: center; color: var(--white);
    font-family: "Roboto", Arial, sans-serif; font-weight: 500;
    font-size: 30px; letter-spacing: 1px;
  }
  .back-url {
    position: absolute; left: 0; right: 0; top: 283px;
    text-align: center; color: var(--white);
    font-size: 13.5px; letter-spacing: 3px;
  }
</style>
</head>
<body>
  <section class="card card--front">
    <svg class="front-shapes" width="600" height="343" viewBox="0 0 600 343">
      <rect class="panel-identity" x="0" y="0" width="344" height="166" fill="var(--forest)"/>
      <polygon class="panel-contacts" points="0,177 344,177 158,343 0,343" fill="var(--emerald)"/>
    </svg>

    <div class="identity">
      <p class="identity__name">DANIEL REYES</p>
      <p class="identity__title">CEO/FOUNDER</p>
      <p class="identity__address">4210 Alder Court<br>Fairbanks, Alaska 99701</p>
    </div>

    <ul class="contacts">
      <li><svg viewBox="0 0 16 16"><path d="M3.6 1l2.6 3-1.5 1.8c.9 2 2.5 3.6 4.5 4.5L11 8.8l3 2.6-1.5 2.6C7 14 2 9 2 3.5z"/></svg>555 210 4817</li>
      <li><svg viewBox="0 0 16 16"><path d="M4 0h8v16H4zM5.5 1.5v11h5v-11z"/></svg>555 386 2290</li>
      <li><svg viewBox="0 0 16 16"><path d="M4 1h8v4H4zM1 6h14v6h-3v3H4v-3H1zM5 10v4h6v-4z"/></svg>555 742 0163</li>
      <li><svg viewBox="0 0 16 16"><path d="M1 3h14v1L8 9 1 4zM1 6l7 5 7-5v7H1z"/></svg>daniel@brightline.com</li>
      <li><svg viewBox="0 0 16 16"><circle cx="8" cy="8" r="7"/><path d="M1 8h14M8 1c3 3 3 11 0 14M8 1c-3 3-3 11 0 14" stroke="var(--emerald)" stroke-width="1.2" fill="none"/></svg>brightline.com</li>
    </ul>

    <div class="company-mark">
      <span class="company-mark__square"></span>
      <span class="company-mark__name">BRIGHTLINE<br>RETROFIT GROUP, LLC</span>
    </div>
  </section>

  <section class="card card--back">
    <p class="back-mark">BRIGHTLINE RETROFIT GROUP, LLC</p>
    <p class="back-url">www.brightlineretrofit.com</p>
  </section>
</body>
</html>
```